Luxury Real Estate Website, Midwest, United States

We need web design services for a luxury website. We need IDX Integration with our MLS. We want this to be a very simple website with amazing graphics. We want it to link up with our MailChimp account in order to generate leads through a "More Information" Pop up on the main page. We want the main page to be covered with one large graphic that is a rolling slideshow of active listings of $400,000 and up from the IDX Integration. We need this website to give a very exclusive and sleek look. Lots of black is good... I will upload our logos in Black and Silver. We will also need an "About" page that we are going to call "Qeno Info". We want our graphics to be extremely impressive. Keep in mind, we are a company in the Midwest of the United States, and our real estate has a different look than homes in California or Florida. We need graphics that are realistic for the Midwest, yet still high-end.
Target Market(s)
Luxury Homeowners in the Midwest United States. The graphics needs to be pristine.
Industry/Entity Type
Real Estate
Coding
Coded - Design and coding required
Number of Pages Required
3 page
Requirements
Must have
- Large graphics with IDX Integration. The photos of real estate need to represent real estate that is common in the Midwest, United States. We also need MailChimp integration. We need a pop up that is titled "My Free Market Analysis" that makes them fill out a contact form asking for Full Name, Email Address, Phone Number and Address. This needs to be a pop up on the front page and will integrate with our MailChimp account. We also need a page called "About Qe No Home". And another page where clients can download informational PDFs. The main component needs to be a front page search engine connected with the IDX to access active listings from our MLS. I attached our logos and a sample front page of a website. I would love for ours to look similar.
Nice to have
- Lake House photos on midwest lakes are a plus.
Should not have
- Should not have clutter. This website needs to be clean, luxurious and exclusive.

```html
<!DOCTYPE html>
<html lang="en">
<head>
<meta charset="utf-8">
<title>Larchmere Realty Group – Luxury Houses</title>
<link href="https://fonts.googleapis.com/css2?family=Lato:ital,wght@0,400;0,700;0,900;1,400&display=swap" rel="stylesheet">
<style>
:root{
  --ink:#1c1c1c;
  --text:#555;
  --muted:#777;
  --steel:#7f8fa8;
  --steel-dark:#6d7e98;
  --pale:#e6ebf3;
  --pale-blue:#c5d1e3;
  --white:#fff;
  --footer:#1a1a1a;
  --footer-line:#2c2c2c;
  --star:#e3a21a;
}
*{margin:0;padding:0;box-sizing:border-box}
html,body{width:1200px;height:3696px;overflow:hidden}
body{font-family:'Lato',sans-serif;color:var(--text);background:var(--white);position:relative}
.abs{position:absolute}

/* header */
.site-header{position:absolute;left:0;top:0;width:1200px;height:98px;background:var(--white)}
.brand{left:99px;top:24px;display:flex;align-items:center;gap:12px}
.brand-mark{width:14px;height:44px;background:var(--ink)}
.brand-name{font-size:22px;font-weight:700;color:var(--ink);line-height:1.05;letter-spacing:.5px}
.brand-name small{display:block;font-size:11px;letter-spacing:2px;font-weight:700}
.account{right:147px;top:12px;display:flex;gap:12px}
.btn-pill{height:36px;padding:0 22px;border-radius:18px;font-size:12px;font-weight:700;display:flex;align-items:center;gap:6px;letter-spacing:.5px}
.btn-login{background:var(--pale-blue);color:var(--ink)}
.btn-signup{border:1.5px solid var(--pale-blue);color:var(--steel)}
.main-nav{right:99px;top:64px;display:flex;gap:42px;font-size:13px;font-weight:700;color:var(--ink);letter-spacing:.3px}

/* hero */
.hero{left:0;top:98px;width:1200px;height:650px;overflow:hidden}
.hero-photo{position:absolute;inset:0;background:linear-gradient(180deg,#b9cbe0 0%,#d7c7a6 28%,#a78f6a 45%,#5d7a3c 62%,#3e6a2c 80%,#2e4f26 100%)}
.hero-title{left:163px;top:206px;width:874px;height:56px;background:#0d0d0d;color:var(--white);font-size:33px;font-weight:900;display:flex;align-items:center;justify-content:center;letter-spacing:.5px}
.hero-search{left:263px;top:318px;width:674px;height:50px;background:var(--white);border-radius:25px;display:flex;align-items:center;padding-left:20px;font-size:14px;color:#444}
.hero-search .go{position:absolute;right:6px;top:6px;width:38px;height:38px;border-radius:50%;background:var(--pale-blue);display:flex;align-items:center;justify-content:center}
.hero-wave{position:absolute;left:0;bottom:0}

/* about */
.section-title{font-size:29px;font-weight:700;color:var(--ink)}
.about-title{left:99px;top:828px}
.about-lead{left:99px;top:877px;width:510px;font-size:16px;font-weight:700;color:#333;line-height:1.55}
.about-body{left:99px;top:958px;width:455px;font-size:13px;line-height:1.85;color:var(--muted)}
.btn-learn{left:99px;top:1140px;width:155px;height:44px;border-radius:22px;background:var(--pale-blue);color:var(--ink);font-size:13px;font-weight:700;display:flex;align-items:center;justify-content:center}
.about-back{left:640px;top:833px;width:461px;height:320px;background:var(--pale-blue)}
.about-photo{left:604px;top:875px;width:455px;height:313px;border:4px solid var(--white);background:linear-gradient(160deg,#9fb6cc 0%,#e8e2d6 40%,#bfa68a 70%,#6e5a48 100%)}

/* services band */
.service-band{left:0;top:1318px;width:1200px;height:427px;background:var(--pale)}
.service-photo{left:99px;top:1286px;width:478px;height:372px;background:linear-gradient(135deg,#3a2a20 0%,#7a5a40 40%,#b88a62 70%,#5a4030 100%)}
.service-card{left:177px;top:1567px;width:227px;height:202px;background:var(--steel);padding:20px 22px;color:var(--white)}
.service-card h3{font-size:20px;font-weight:400;line-height:1.25}
.service-card p{font-size:11px;margin-top:12px;line-height:1.5;color:#e8ecf3}
.dots{display:flex;gap:6px;margin-top:18px}
.dots i{width:9px;height:9px;border-radius:50%;border:1.5px solid var(--white)}
.dots i.on{background:var(--white)}
.feature{left:631px;width:470px}
.feature h3{font-size:21px;font-weight:700;color:var(--ink)}
.feature p{font-size:12.5px;line-height:1.75;color:var(--muted);margin-top:14px}
.feature a{display:block;margin-top:10px;font-size:12px;font-weight:700;color:var(--ink);text-decoration:none}

/* places */
.places-title{left:0;top:1820px;width:1200px;text-align:center}
.places-sub{left:0;top:1870px;width:1200px;text-align:center;font-size:13px;font-style:italic;color:#444}
.place{top:1929px;width:322px;height:358px;border:1px solid #e2e2e2;background:var(--white)}
.place-photo{height:247px}
.place h4{font-size:14px;font-weight:700;color:var(--ink);margin:20px 0 0 20px}
.place p{display:flex;gap:10px;font-size:12.5px;color:#555;line-height:1.5;margin:12px 20px 0 20px}
.slider-bars{left:527px;top:2323px;display:flex;gap:10px}
.slider-bars i{width:42px;height:5px;background:var(--steel)}
.slider-bars i.off{background:var(--pale-blue)}

/* call to action */
.cta{left:0;top:2427px;width:1200px;height:333px;background:linear-gradient(180deg,#4a5258 0%,#3b4740 45%,#2d3a2c 75%,#25302a 100%)}
.cta h2{position:absolute;top:72px;width:1200px;text-align:center;font-size:29px;font-weight:700;color:var(--white)}
.cta p{position:absolute;top:126px;left:300px;width:600px;text-align:center;font-size:12.5px;font-style:italic;line-height:1.9;color:#e6e6e6}
.cta-actions{position:absolute;top:210px;width:1200px;display:flex;justify-content:center;gap:14px}
.cta-actions span{height:42px;padding:0 24px;border-radius:21px;display:flex;align-items:center;font-size:14px;font-weight:700}
.btn-buy{background:var(--pale-blue);color:var(--ink)}
.btn-more{border:2px solid var(--white);color:var(--white)}

/* testimonial + partners */
.testi-title{left:99px;top:2843px;font-size:25px}
.testi-card{left:99px;top:2927px;width:485px;height:210px;border:1px solid #ccc;padding:30px 24px 0 22px}
.testi-card p{font-size:11.5px;font-style:italic;line-height:1.85;color:#444;width:410px}
.testi-name{margin-top:14px;font-size:15px;color:var(--ink)}
.testi-name small{font-size:11px;color:#777;margin-left:6px}
.stars{color:var(--star);font-size:14px;letter-spacing:1px;margin-top:4px}
.quote-badge{left:508px;top:2900px;width:54px;height:54px;border-radius:50%;background:var(--steel-dark);display:flex;align-items:center;justify-content:center}
.avatar{left:482px;top:3044px;width:76px;height:76px;border-radius:50%;border:3px solid var(--white);background:linear-gradient(180deg,#c9ccd1,#8a8f99);box-shadow:0 0 0 1px #ddd}
.testi-nav{left:524px;top:3152px;display:flex;gap:8px}
.testi-nav i{width:24px;height:24px;border-radius:50%;background:var(--ink);display:flex;align-items:center;justify-content:center}
.partners-title{left:631px;top:2843px;font-size:25px}
.partners{left:621px;top:2902px;width:480px;height:203px;display:grid;grid-template-columns:repeat(3,1fr);grid-template-rows:1fr 1fr}
.partners div{display:flex;align-items:center;justify-content:center;border-right:1px solid #e4e4e4;border-bottom:1px solid #e4e4e4}
.partners div:nth-child(3n){border-right:none}
.partners div:nth-child(n+4){border-bottom:none}
.partners span{width:110px;height:54px;border-radius:4px;background:var(--pale)}

/* footer */
.site-footer{left:0;top:3272px;width:1200px;height:424px;background:var(--footer);color:#9a9a9a}
.site-footer h5{position:absolute;top:84px;font-size:18px;font-weight:700;color:var(--white);letter-spacing:.3px}
.quick-links{position:absolute;left:99px;top:130px;list-style:none;font-size:12px;line-height:24px}
.quick-links li::before{content:"›";margin-right:14px;color:#666}
.contact-list{position:absolute;left:313px;top:128px;font-size:11.5px;line-height:1.6}
.contact-list div{display:flex;gap:14px;margin-bottom:22px}
.contact-list svg{flex:none;margin-top:2px}
.news-input{position:absolute;left:626px;top:131px;width:262px;height:38px;background:var(--white);font-size:11.5px;color:#555;padding:12px 10px}
.news-btn{position:absolute;left:626px;top:185px;width:136px;height:40px;background:#555;color:var(--white);font-size:12px;font-weight:700;display:flex;align-items:center;justify-content:center}
.follow{position:absolute;left:979px;top:127px;font-size:12px}
.follow div{display:flex;align-items:center;gap:14px;margin-bottom:13px}
.follow i{width:34px;height:34px;border-radius:50%;display:block}
.copyright{position:absolute;left:0;top:370px;width:1200px;border-top:1px solid var(--footer-line);padding-top:18px;text-align:center;font-size:11px;color:#777}
.side-tab{left:1142px;top:3363px;width:58px;height:224px;background:var(--pale);border-radius:14px 0 0 14px;display:flex;align-items:center;justify-content:center}
.side-tab span{transform:rotate(-90deg);white-space:nowrap;font-size:12px;font-weight:700;color:var(--ink);letter-spacing:1px}
</style>
</head>
<body>

<header class="site-header">
  <div class="abs brand"><span class="brand-mark"></span><span class="brand-name">LARCHMERE<small>REALTY GROUP</small></span></div>
  <div class="abs account">
    <span class="btn-pill btn-login"><svg width="10" height="12" viewBox="0 0 10 12"><rect x="1" y="5" width="8" height="7" fill="#1c1c1c"/><path d="M3 5V3a2 2 0 0 1 4 0v2" stroke="#1c1c1c" stroke-width="1.5" fill="none"/></svg>LOGIN</span>
    <span class="btn-pill btn-signup"><svg width="11" height="10" viewBox="0 0 11 10"><path d="M1 5h6M5 2l3 3-3 3" stroke="#7f8fa8" stroke-width="1.5" fill="none"/></svg>SIGNUP</span>
  </div>
  <nav class="abs main-nav"><span>HOME</span><span>QENO INFO</span><span>ABOUT QE NO HOME</span><span>DOWNLOADS</span><span>CONTACT US</span></nav>
</header>

<section class="abs hero">
  <div class="hero-photo" role="img" aria-label="Large Midwest brick and stucco luxury homes with lawn, trees and a lake fountain"></div>
  <h1 class="abs hero-title">LUXURY HOUSES FROM MIDWEST, UNITED STATES</h1>
  <div class="abs hero-search">Search homes by city &amp; state,zip, or MLS#
    <span class="go"><svg width="14" height="14" viewBox="0 0 14 14"><circle cx="6" cy="6" r="4" stroke="#1c1c1c" stroke-width="2" fill="none"/><path d="M9 9l4 4" stroke="#1c1c1c" stroke-width="2"/></svg></span>
  </div>
  <svg class="hero-wave" width="1200" height="110" viewBox="0 0 1200 110">
    <path d="M0 40 Q300 110 600 60 T1200 30 V110 H0Z" fill="#c5d1e3"/>
    <path d="M0 60 Q320 130 620 80 T1200 55 V110 H0Z" fill="#fff"/>
  </svg>
</section>

<section>
  <h2 class="abs section-title about-title">About Qe No Home</h2>
  <p class="abs about-lead">Sed ut perspiciatis unde omnis iste natus error sit voluptatem accusantium doloremque laudantium</p>
  <p class="abs about-body">Lorem ipsum dolor sit amet, consectetur adipiscing elit, sed do eiusmod tempor incididunt ut labore et dolore magna aliqua. Ut enim ad minim dolor veniam, quis nostrud exercitation ullamco laboris nisi ut aliquip execute that commodo consequat. Duis aute irure dolor in reprehenderit in voluptate velit esse cillum dolore eu fugiat nulla pariatur. Excepteur sint occaecat cupidatat non proident, sunt in culpa qui officia deserunt mollit anim id est laborum.</p>
  <span class="abs btn-learn">LEARN MORE &gt;&gt;</span>
  <div class="abs about-back"></div>
  <div class="abs about-photo" role="img" aria-label="Bright living room with white sofa and lake and mountain view"></div>
</section>

<section>
  <div class="abs service-band"></div>
  <div class="abs service-photo" role="img" aria-label="Group of clients meeting with an agent in a warm lounge"></div>
  <div class="abs service-card">
    <h3>Nemo enim ipsam voluptatem dolor voluptas sit</h3>
    <p>sed quia non numquam eius modi tempora incidunt</p>
    <div class="dots"><i></i><i class="on"></i><i class="on"></i></div>
  </div>
  <div class="abs feature" style="top:1376px">
    <h3>Customer Satisfaction</h3>
    <p>Lorem ipsum dolor sit amet, consectetur adipiscing elit, sed do eiusmod tempor incididunt ut labore et dolore magna aliqua. Ut enim ad minim veniam, quis nostrud exercitation ullamco laboris nisi ut aliquip.</p>
    <a>Learn More &gt;&gt;</a>
  </div>
  <div class="abs feature" style="top:1538px">
    <h3>Best Service Certification</h3>
    <p>Lorem ipsum dolor sit amet, consectetur adipiscing elit, sed do eiusmod tempor incididunt ut labore et dolore magna aliqua. Ut enim ad minim veniam, quis nostrud exercitation ullamco laboris nisi ut aliquip.</p>
    <a>Learn More &gt;&gt;</a>
  </div>
</section>

<section>
  <h2 class="abs section-title places-title">Most Popular Places</h2>
  <p class="abs places-sub">Lorem ipsum dolor sit amet, consectetur adipiscing elit, sed do eiusmod tempor</p>
  <article class="abs place" style="left:99px">
    <div class="place-photo" role="img" aria-label="White lakeside villa with lawn under a blue sky" style="background:linear-gradient(180deg,#8fb1d8 0%,#e9ecef 45%,#6f8f4a 75%,#4c6b32 100%)"></div>
    <h4>Labore et dolore magna aliqua. Ut enim</h4>
    <p><svg width="10" height="13" viewBox="0 0 10 13"><path d="M5 0a4.5 4.5 0 0 0-4.5 4.5C.5 8 5 13 5 13s4.5-5 4.5-8.5A4.5 4.5 0 0 0 5 0z" fill="#333"/><circle cx="5" cy="4.5" r="1.6" fill="#fff"/></svg>Error sit voluptatem accusantium doloremque laudantium, totam rem aperiam, eaque ipsa</p>
  </article>
  <article class="abs place" style="left:439px">
    <div class="place-photo" role="img" aria-label="Poolside terrace with sun umbrellas framed by curtains" style="background:linear-gradient(180deg,#cfd8df 0%,#9cc2d9 40%,#3fa6c9 70%,#c8b8a2 100%)"></div>
    <h4>Labore et dolore magna aliqua. Ut enim</h4>
    <p><svg width="10" height="13" viewBox="0 0 10 13"><path d="M5 0a4.5 4.5 0 0 0-4.5 4.5C.5 8 5 13 5 13s4.5-5 4.5-8.5A4.5 4.5 0 0 0 5 0z" fill="#333"/><circle cx="5" cy="4.5" r="1.6" fill="#fff"/></svg>Error sit voluptatem accusantium doloremque laudantium, totam rem aperiam, eaque ipsa</p>
  </article>
  <article class="abs place" style="left:779px">
    <div class="place-photo" role="img" aria-label="Modern lounge with grey sofa and red cushions facing a lake" style="background:linear-gradient(160deg,#6b7a8a 0%,#a9b9c6 40%,#d9d6d0 65%,#6d6a66 100%)"></div>
    <h4>Labore et dolore magna aliqua. Ut enim</h4>
    <p><svg width="10" height="13" viewBox="0 0 10 13"><path d="M5 0a4.5 4.5 0 0 0-4.5 4.5C.5 8 5 13 5 13s4.5-5 4.5-8.5A4.5 4.5 0 0 0 5 0z" fill="#333"/><circle cx="5" cy="4.5" r="1.6" fill="#fff"/></svg>Error sit voluptatem accusantium doloremque laudantium, totam rem aperiam, eaque ipsa</p>
  </article>
  <div class="abs slider-bars"><i></i><i class="off"></i><i></i></div>
</section>

<section class="abs cta" role="img" aria-label="Dusk view of a lakeside home row with lawn and water">
  <h2>Looking for best home ever!</h2>
  <p>Sed ut perspiciatis unde omnis iste natus error sit voluptatem accusantium doloremque laudantium, totam. Nemo enim ipsam voluptatem quia voluptas sit aspernatur aut odit aut fugit.</p>
  <div class="cta-actions"><span class="btn-buy">Purchase Now</span><span class="btn-more">View More Info</span></div>
</section>

<section>
  <h2 class="abs section-title testi-title">Testimonial</h2>
  <div class="abs testi-card">
    <p>Sed ut perspiciatis unde omnis iste natus error sit voluptatem accusantium doloremque laudantium, totam rem aperiam, eaque ipsa quae ab illo inventore veritatis et quasi architecto beatae vitae dicta sunt explicabo. Nemo enim ipsam voluptatem quia voluptas sit aspernatur</p>
    <div class="testi-name">Sit voluptatem <small>- City Location</small></div>
    <div class="stars">★★★★★</div>
  </div>
  <div class="abs quote-badge"><svg width="24" height="18" viewBox="0 0 24 18"><path d="M0 18V10C0 4 3 1 9 0v4c-3 1-4 3-4 6h4v8zM14 18V10c0-6 3-9 9-10v4c-3 1-4 3-4 6h4v8z" fill="#fff"/></svg></div>
  <div class="abs avatar" role="img" aria-label="Client portrait"></div>
  <div class="abs testi-nav">
    <i><svg width="8" height="10" viewBox="0 0 8 10"><path d="M6 1L2 5l4 4" stroke="#fff" stroke-width="2" fill="none"/></svg></i>
    <i><svg width="8" height="10" viewBox="0 0 8 10"><path d="M2 1l4 4-4 4" stroke="#fff" stroke-width="2" fill="none"/></svg></i>
  </div>
  <h2 class="abs section-title partners-title">Our Partners</h2>
  <div class="abs partners" role="list" aria-label="Partner badges">
    <div><span></span></div><div><span></span></div><div><span></span></div>
    <div><span></span></div><div><span></span></div><div><span></span></div>
  </div>
</section>

<footer class="abs site-footer">
  <h5 style="left:99px">QUICK LINKS</h5>
  <ul class="quick-links"><li>Home</li><li>Qeno Info</li><li>About Qe No Home</li><li>Downloads</li><li>Contact us</li></ul>
  <h5 style="left:313px">CONTACT US</h5>
  <div class="contact-list">
    <div><svg width="10" height="10" viewBox="0 0 10 10"><path d="M10 0L0 4l4 2 2 4z" fill="#888"/></svg><span>#123 Building Name City Location,<br>Landmark, Zipcode</span></div>
    <div><svg width="11" height="11" viewBox="0 0 11 11"><path d="M2 0l2 3-1 1c1 2 2 3 4 4l1-1 3 2-1 2C5 11 0 6 0 2z" fill="#888"/></svg><span>01555 210376</span></div>
    <div><svg width="12" height="9" viewBox="0 0 12 9"><rect width="12" height="9" fill="#888"/><path d="M0 0l6 5 6-5" stroke="#1a1a1a" fill="none"/></svg><span>info@larchmererealty.com</span></div>
  </div>
  <h5 style="left:626px">NEWSLETTER</h5>
  <div class="news-input">Email ID</div>
  <div class="news-btn">SUBSCRIBE</div>
  <h5 style="left:979px">FOLLOW US</h5>
  <div class="follow">
    <div><i style="background:#3b5998"></i>Linkbook</div>
    <div><i style="background:#1da1f2"></i>Chirper</div>
    <div><i style="background:#dd4b39"></i>Circlesphere</div>
    <div><i style="background:#cc181e"></i>Streamtube</div>
  </div>
  <div class="copyright">Copyright © 2018 Larchmere Realty Group . All Rights Reserved.</div>
</footer>

<div class="abs side-tab"><span>GET TO KNOW US</span></div>

</body>
</html>
```